UI Improvement for FlorKeep app

We are looking for a talented UI/UX designer to REFINE and enhance the visual design of our mobile application, FlorKeep. The app is fully functional, but we need a designer to improve its aesthetics by specifying design elements such as fonts, colors, spacing, and component styles.
Your task will be to analyze the CURRENT UI and provide detailed design specifications that will make the app more visually appealing, modern, and user-friendly.
TODO:
Review the existing FlorKeep app design (see attachments) and identify areas for visual improvement.
Provide a detailed UI style guide, including:
Typography (font choices, sizes, and weights)
Color palette (primary, secondary, and accent colors)
Component styling (buttons, forms, icons, and interactive elements)
Spacing and layout guidelines (margins, paddings, and alignment)
Ensure the design remains clean, modern, and professional while maintaining usability and accessibility.
Provide design mockups or visual examples (if possible) to illustrate the proposed changes.
Deliverables:
A UI Style Guide (PDF or Figma file) with specifications on fonts, colors, spacing, and UI components.
Optionally, before/after mockups or examples demonstrating the improvements.
Ideal Designer:
Strong experience in mobile UI/UX design.
Understanding of modern design trends and best practices.
Ability to communicate design choices clearly for easy developer implementation.
I have attached 7 images showcasing the main UI screens used in the FlorKeep app. These screens need visual enhancements to improve their overall look and user experience.
The images represent the current design in three key modes:
LIST Mode – Displays data in a structured list format.
READ Mode – Shows detailed information when a user selects an item.
ADD/EDIT Mode – Allows users to input or modify information.
Additionally, there is a ‘MORE’ page, which serves as a menu listing other features of the application.
Task Objective:
Please refine and improve these UIs to create a more modern, visually appealing, and user-friendly experience. Focus on typography, colors, spacing, and component styling to ensure a cohesive and polished design.
Look and feel
Each slider illustrates characteristics of the customer's brand and the style your logo design should communicate.

```html
<!DOCTYPE html>
<html lang="en">
<head>
<meta charset="utf-8">
<title>FlorKeep – UI screens</title>
<link href="https://fonts.googleapis.com/css2?family=Inter:wght@400;500;600;700&display=swap" rel="stylesheet">
<style>
:root{
  --canvas:#dedede;
  --ink:#1d2330;
  --muted:#9aa3b2;
  --primary:#1452b3;
  --primary-2:#1e63cc;
  --accent:#2a7bf5;
  --surface:#f2f5f9;
  --card:#ffffff;
  --line:#e6eaf0;
  --chip-blue:#dbeafe;
  --chip-green:#dcf7e4;
  --chip-grey:#eceff3;
  --teal:#10a37f;
  --green-text:#2f9b2f;
  --yellow:#fff8b8;
  --sky:#bfe0fb;
  --mint:#b9f1b3;
  --deep:#1249a6;
}
*{box-sizing:border-box;margin:0;padding:0}
html,body{width:686px;height:1200px;overflow:hidden;background:var(--canvas);font-family:"Inter",sans-serif;color:var(--ink)}
.stage{position:absolute;left:0;top:0;width:1456px;height:2546px;transform:scale(.47115);transform-origin:0 0}
.label{position:absolute;text-align:center;font-weight:700;font-size:20px;letter-spacing:.3px;line-height:1.3;color:#222}
.label span{display:block;font-size:19px;margin-top:8px}
.label .soft{color:#8a8a8a;font-weight:600}
.screen{position:absolute;width:212px;background:var(--surface);border-radius:26px;overflow:hidden;font-size:8px}
.screen.white{background:var(--card)}
.hero{position:relative;height:78px;background:var(--primary)}
.hero-photo{position:absolute;inset:0;background:linear-gradient(160deg,#2d6fd0 0%,#1452b3 55%,#0f47a0 100%)}
.status{position:absolute;top:14px;left:14px;right:14px;display:flex;justify-content:space-between;color:#fff;font-size:7px}
.status i{display:inline-block;width:11px;height:5px;border:1px solid #fff;border-radius:2px;margin-left:3px}
.bar{position:absolute;top:38px;left:12px;right:12px;height:16px;display:flex;align-items:center;color:#fff}
.bar .back,.bar .dots{width:13px;height:13px;border-radius:50%;background:rgba(255,255,255,.3);display:flex;align-items:center;justify-content:center;font-size:7px;flex:none}
.bar .title{flex:1;text-align:center;font-size:11.5px;font-weight:600}
.bar .title.left{text-align:left}
.bar .pill{background:rgba(255,255,255,.35);border-radius:8px;padding:2px 9px;font-size:7px;font-weight:600;margin-right:5px}
.body{position:relative;margin-top:-10px;padding:0 8px}
.card{background:var(--card);border-radius:10px;padding:10px 8px 6px}
.card-head{display:flex;justify-content:space-between;align-items:center;font-size:9px;font-weight:500;margin-bottom:8px;color:#333}
.card-head em{font-style:normal;color:#bbb}
.section{display:flex;justify-content:space-between;font-size:9px;font-weight:500;margin:12px 4px 8px;color:#333}
.field{display:flex;align-items:center;gap:10px;background:var(--card);border:1px solid var(--line);border-radius:6px;height:32px;padding:0 8px;margin-bottom:7px}
.field small{display:block;font-size:5.5px;color:var(--muted);margin-bottom:3px}
.field b{font-weight:500;font-size:7.5px}
.field .grow{flex:1}
.field .chev{color:#555;font-size:7px}
.row2{display:flex;gap:7px}
.row2 .field{flex:1}
.i{width:12px;height:12px;flex:none;color:#a9b0bb}
.ring{width:16px;height:16px;border-radius:50%;background:var(--chip-blue);display:flex;align-items:center;justify-content:center;flex:none}
.ring .i{width:9px;height:9px;color:var(--primary)}
.star{color:var(--primary);font-size:6px}
.nav{position:absolute;left:0;right:0;bottom:0;height:40px;background:var(--card);display:flex;align-items:center;justify-content:space-around;padding:0 10px}
.nav.blue{background:var(--primary)}
.nav .on{background:var(--accent);color:#fff;border-radius:10px;padding:4px 9px;font-size:7px;font-weight:600;display:flex;align-items:center;gap:4px}
.nav .on i{width:8px;height:8px;background:#fff;border-radius:2px}
.nav .ico{width:11px;height:11px;border-radius:3px;background:#c8d8f3}
.nav.blue .ico{background:#3e86f0}
.nav.blue .on{background:#fff;color:var(--primary)}
.nav.blue .on i{background:var(--primary)}
.nav .tab{display:flex;flex-direction:column;align-items:center;gap:3px;font-size:5.5px;color:#6fa1ec}
.nav .tab.cur{color:#fff}
.nav .tab .ico{background:#4a8ef0}
.nav .tab.cur .ico{background:#fff}
/* lists */
.search{display:flex;align-items:center;gap:6px;background:var(--card);border-radius:8px;height:26px;padding:0 8px;font-size:7px;color:#555;margin-bottom:4px}
.search .grow{flex:1}
.search .sel{border-right:1px solid var(--line);padding-right:8px;display:flex;gap:8px}
.filter{width:14px;height:14px;border-radius:50%;background:var(--accent)}
.letter{display:flex;justify-content:space-between;font-size:8px;color:#444;margin:8px 6px 6px}
.item{display:flex;align-items:center;gap:8px;background:var(--card);border-radius:6px;padding:7px 8px;margin-bottom:6px;min-height:44px}
.avatar{width:30px;height:30px;border-radius:50%;flex:none;background:linear-gradient(135deg,#34495e,#7d93b1)}
.item .grow{flex:1}
.item .name{font-size:7.5px;margin-bottom:5px}
.item .date{font-size:6px;color:#b4bac4;align-self:flex-end}
.tags{display:flex;gap:4px;flex-wrap:wrap}
.tag{font-size:5.5px;padding:2px 5px;border-radius:6px;font-weight:600}
.t-id{background:var(--chip-blue);color:var(--primary)}
.t-own{background:#e6faf4;color:var(--teal)}
.t-ent{background:var(--chip-blue);color:var(--primary)}
.t-qual{background:var(--chip-green);color:var(--green-text)}
.t-pilot{background:var(--chip-grey);color:#666}
/* read */
.action{display:flex;align-items:center;gap:10px;background:var(--card);border-radius:5px;height:27px;padding:0 10px;font-size:7.5px;margin-bottom:7px}
.block{border-radius:5px;padding:9px 6px 8px;margin-bottom:7px;font-size:7.5px}
.block.y{background:var(--yellow)}.block.b{background:var(--sky)}.block.g{background:var(--mint)}
.block .drop{background:var(--card);border-radius:4px;display:flex;align-items:center;justify-content:space-between;padding:6px 8px;font-size:6.5px;line-height:1.5;margin:9px 0 7px}
.btn{display:inline-block;background:var(--deep);color:#fff;border-radius:8px;font-size:6.5px;font-weight:600;padding:2px 8px}
.btn.full{display:block;text-align:center}
.menu{background:var(--card);border-radius:10px;padding:4px 8px}
.menu div{display:flex;align-items:center;gap:12px;height:29px;border-bottom:1px solid var(--line);font-size:7.5px}
.menu div:last-child{border-bottom:0}
.menu .ring{background:#dde8fb}
.box{background:var(--card);border-radius:5px;padding:4px 8px;margin-bottom:8px}
.box .field{border:0;border-bottom:1px solid var(--line);border-radius:0;margin:0;height:38px;padding:0}
.box .field:last-child{border-bottom:0}
.pointer{position:absolute;left:855px;top:2236px;width:3px;height:28px;background:#222}
</style>
</head>
<body>
<svg width="0" height="0" style="position:absolute" aria-hidden="true">
  <defs>
    <symbol id="user" viewBox="0 0 12 12"><circle cx="6" cy="4" r="2.3" fill="none" stroke="currentColor"/><path d="M2 11c0-2.4 1.8-3.8 4-3.8s4 1.4 4 3.8" fill="none" stroke="currentColor"/></symbol>
    <symbol id="pin" viewBox="0 0 12 12"><path d="M6 11S2.5 7.3 2.5 4.8a3.5 3.5 0 0 1 7 0C9.5 7.3 6 11 6 11z" fill="none" stroke="currentColor"/><circle cx="6" cy="4.8" r="1.2" fill="none" stroke="currentColor"/></symbol>
    <symbol id="case" viewBox="0 0 12 12"><rect x="1.5" y="3.5" width="9" height="7" rx="1.2" fill="none" stroke="currentColor"/><path d="M4.5 3.5V2h3v1.5M1.5 6.5h9" fill="none" stroke="currentColor"/></symbol>
    <symbol id="bld" viewBox="0 0 12 12"><rect x="2" y="2" width="8" height="9" fill="none" stroke="currentColor"/><path d="M4 4h1M7 4h1M4 6h1M7 6h1M5 11V8.5h2V11" fill="none" stroke="currentColor"/></symbol>
    <symbol id="mail" viewBox="0 0 12 12"><rect x="1.5" y="3" width="9" height="6.5" rx="1" fill="none" stroke="currentColor"/><path d="M1.5 3.5 6 7l4.5-3.5" fill="none" stroke="currentColor"/></symbol>
    <symbol id="phone" viewBox="0 0 12 12"><path d="M3 1.5l2 2.2-1 1.3a6 6 0 0 0 3 3l1.3-1 2.2 2L9.3 10.5C5 10.5 1.5 7 1.5 2.7z" fill="none" stroke="currentColor"/></symbol>
    <symbol id="star" viewBox="0 0 12 12"><path d="M6 1.5l1.3 2.9 3.1.3-2.3 2.1.7 3.1L6 8.3 3.2 9.9l.7-3.1L1.6 4.7l3.1-.3z" fill="none" stroke="currentColor"/></symbol>
    <symbol id="plane" viewBox="0 0 12 12"><path d="M1 7l10-4-2 7-2.5-2.5L5 9.5 4.5 6.5z" fill="none" stroke="currentColor"/></symbol>
    <symbol id="shield" viewBox="0 0 12 12"><path d="M6 1.5l4 1.5v3c0 2.5-1.8 4-4 4.8C3.8 10 2 8.5 2 6V3z" fill="none" stroke="currentColor"/></symbol>
    <symbol id="cal" viewBox="0 0 12 12"><rect x="1.5" y="2.5" width="9" height="8" rx="1" fill="none" stroke="currentColor"/><path d="M1.5 5h9M4 1.5v2M8 1.5v2" fill="none" stroke="currentColor"/></symbol>
    <symbol id="gear" viewBox="0 0 12 12"><circle cx="6" cy="6" r="2" fill="none" stroke="currentColor"/><circle cx="6" cy="6" r="4.2" fill="none" stroke="currentColor" stroke-dasharray="2 1.3"/></symbol>
    <symbol id="arrow" viewBox="0 0 12 12"><circle cx="6" cy="6" r="4.5" fill="none" stroke="currentColor"/><path d="M4 6h4M6.5 4.2 8.2 6 6.5 7.8" fill="none" stroke="currentColor"/></symbol>
  </defs>
</svg>

<main class="stage">

  <!-- Row 1 labels -->
  <div class="label" style="left:140px;top:110px;width:200px">ADD ACCOUNT<span class="soft">RADS_ADDEDIT_PAGE</span></div>
  <div class="label" style="left:404px;top:110px;width:240px">ADD ACCOUNT - OPTION ONE</div>
  <div class="label" style="left:703px;top:110px;width:260px">ADD ACCOUNT - OPTION TWO</div>
  <div class="label" style="left:1100px;top:102px;width:200px">MORE<span>RADS_MORE_PAGE</span></div>

  <!-- Add Contact -->
  <section class="screen" style="left:140px;top:178px;height:552px">
    <header class="hero"><div class="hero-photo" role="img" aria-label="Aerial photo of an airliner above a runway"></div>
      <div class="status"><span>12:30PM</span><span>▂▄ ◠<i></i></span></div>
      <div class="bar"><span class="back">‹</span><span class="title">Add Contact</span><span class="pill">Save</span><span class="dots">···</span></div>
    </header>
    <div class="body">
      <div class="card">
        <div class="card-head">Contact Information<em>···</em></div>
        <div class="field"><svg class="i"><use href="#case"/></svg><div><small>Business Name -e</small><b>Contact Business name</b></div></div>
        <div class="field"><svg class="i"><use href="#user"/></svg><div><small>First Name -e</small><b>Daniel</b></div></div>
        <div class="field"><svg class="i"><use href="#user"/></svg><div><small>Middle Name -e</small><b>Lorne</b></div></div>
        <div class="field"><svg class="i"><use href="#user"/></svg><div><small>Last Name -e</small><b>Whitaker</b></div></div>
        <div class="section">Address Information<span>⌄</span></div>
        <div class="field"><svg class="i"><use href="#pin"/></svg><div class="grow"><small>Address Label Tag -e</small><b>Address</b></div><span class="chev">⌄</span></div>
        <div class="field"><svg class="i"><use href="#pin"/></svg><div><small>Address Line1 -e <span class="star">★</span></small><b>Daniel</b></div></div>
        <div class="field"><svg class="i"><use href="#pin"/></svg><div><small>Address Line2 -e <span class="star">★</span></small><b>Lorne</b></div></div>
        <div class="field"><svg class="i"><use href="#bld"/></svg><div><small>Address City</small><b>Harbor City, HC</b></div></div>
        <div class="row2"><div class="field"><div class="grow"><small>AddressState</small><b>Harbor State</b></div><span class="chev">⌄</span></div><div class="field"><div><small>Zip -e</small><b>40517</b></div></div></div>
      </div>
    </div>
    <nav class="nav"><span class="on"><i></i>Contact</span><span class="ico"></span><span class="ico"></span><span class="ico"></span><span class="ico"></span></nav>
  </section>

  <!-- Option one -->
  <section class="screen" style="left:436px;top:178px;height:552px">
    <header class="hero"><div class="hero-photo" role="img" aria-label="Aerial photo of an airliner above a runway"></div>
      <div class="status"><span>12:30PM</span><span>▂▄ ◠<i></i></span></div>
      <div class="bar"><span class="back">‹</span><span class="title">Add Contact</span><span class="pill">Save</span><span class="dots">···</span></div>
    </header>
    <div class="body" style="padding-top:14px;margin-top:0;background:var(--surface)">
      <div class="card-head" style="margin:0 6px 8px">Contact Information<em>···</em></div>
      <div class="field"><svg class="i"><use href="#case"/></svg><div><small>Business Name -e</small><b>Contact Business name</b></div></div>
      <div class="field"><svg class="i"><use href="#user"/></svg><div><small>First Name -e</small><b>Daniel</b></div></div>
      <div class="field"><svg class="i"><use href="#user"/></svg><div><small>Middle Name -e</small><b>Lorne</b></div></div>
      <div class="field"><svg class="i"><use href="#user"/></svg><div><small>Last Name -e</small><b>Whitaker</b></div></div>
      <div class="section">Address Information<span>⌄</span></div>
      <div class="field"><svg class="i"><use href="#pin"/></svg><div class="grow"><small>Address Label Tag -e</small><b>Address</b></div><span class="chev">⌄</span></div>
      <div class="field"><svg class="i"><use href="#pin"/></svg><div><small>Address Line1 -e <span class="star">★</span></small><b>Daniel</b></div></div>
      <div class="field"><svg class="i"><use href="#pin"/></svg><div><small>Address Line2 -e <span class="star">★</span></small><b>Lorne</b></div></div>
      <div class="field"><svg class="i"><use href="#bld"/></svg><div><small>Address City</small><b>Harbor City, HC</b></div></div>
      <div class="row2"><div class="field"><svg class="i"><use href="#pin"/></svg><div class="grow"><small>AddressState</small><b>Harbor State</b></div><span class="chev">⌄</span></div><div class="field"><svg class="i"><use href="#bld"/></svg><div><small>Zip -e</small><b>40517</b></div></div></div>
    </div>
    <nav class="nav"><span class="on"><i></i>Contact</span><span class="ico"></span><span class="ico"></span><span class="ico"></span><span class="ico"></span></nav>
  </section>

  <!-- Option two -->
  <section class="screen" style="left:737px;top:178px;height:557px">
    <header class="hero"><div class="hero-photo" role="img" aria-label="Aerial photo of an airliner above a runway"></div>
      <div class="status"><span>12:30PM</span><span>▂▄ ◠<i></i></span></div>
      <div class="bar"><span class="back">‹</span><span class="title">Add Contact</span><span class="pill">Save</span><span class="dots">···</span></div>
    </header>
    <div class="body" style="padding-top:14px;margin-top:0">
      <div class="card-head" style="margin:0 6px 8px">Contact Information<em>···</em></div>
      <div class="field"><span class="ring"><svg class="i"><use href="#case"/></svg></span><div><small>Business Name -e</small><b>Contact Business name</b></div></div>
      <div class="field"><span class="ring"><svg class="i"><use href="#user"/></svg></span><div><small>First Name -e</small><b>Daniel</b></div></div>
      <div class="field"><span class="ring"><svg class="i"><use href="#user"/></svg></span><div><small>Middle Name -e</small><b>Lorne</b></div></div>
      <div class="field"><span class="ring"><svg class="i"><use href="#user"/></svg></span><div><small>Last Name -e</small><b>Whitaker</b></div></div>
      <div class="section">Address Information<span>⌄</span></div>
      <div class="field"><span class="ring"><svg class="i"><use href="#pin"/></svg></span><div class="grow"><small>Address Label Tag -e</small><b>Address</b></div><span class="chev">⌄</span></div>
      <div class="field"><span class="ring"><svg class="i"><use href="#pin"/></svg></span><div><small>Address Line1 -e <span class="star">★</span></small><b>88 Alder Road</b></div></div>
      <div class="field"><span class="ring"><svg class="i"><use href="#pin"/></svg></span><div><small>Address Line2 -e <span class="star">★</span></small><b>212 Birch Lane, Apt 4</b></div></div>
      <div class="field"><span class="ring"><svg class="i"><use href="#bld"/></svg></span><div><small>Address City</small><b>Harbor City, HC</b></div></div>
      <div class="row2"><div class="field"><div class="grow"><small>AddressState</small><b>Harbor State</b></div><span class="chev">⌄</span></div><div class="field"><div><small>Zip -e</small><b>40517</b></div></div></div>
    </div>
    <nav class="nav"><span class="on"><i></i>Contact</span><span class="ico"></span><span class="ico"></span><span class="ico"></span><span class="ico"></span></nav>
  </section>

  <!-- More -->
  <section class="screen" style="left:1090px;top:178px;height:437px">
    <header class="hero"><div class="hero-photo" role="img" aria-label="Aerial photo of an airliner above a runway"></div>
      <div class="status"><span>12:30PM</span><span>▂▄ ◠<i></i></span></div>
      <div class="bar"><span class="title left">More</span><span class="dots">···</span></div>
    </header>
    <div class="body" style="padding-top:18px;margin-top:0">
      <div class="menu">
        <div><span class="ring"><svg class="i"><use href="#plane"/></svg></span>Flight</div>
        <div><span class="ring"><svg class="i"><use href="#arrow"/></svg></span>Login</div>
        <div><span class="ring"><svg class="i"><use href="#user"/></svg></span>Account</div>
        <div><span class="ring"><svg class="i"><use href="#cal"/></svg></span>Calendar</div>
        <div><span class="ring"><svg class="i"><use href="#user"/></svg></span>Users</div>
        <div><span class="ring"><svg class="i"><use href="#bld"/></svg></span>Dashboard</div>
        <div><span class="ring"><svg class="i"><use href="#pin"/></svg></span>Tracking</div>
        <div><span class="ring"><svg class="i"><use href="#star"/></svg></span>Outreach Event</div>
        <div><span class="ring"><svg class="i"><use href="#shield"/></svg></span>Maintenance Resource</div>
        <div><span class="ring"><svg class="i"><use href="#gear"/></svg></span>Setting</div>
      </div>
    </div>
    <nav class="nav"><span class="ico"></span><span class="ico"></span><span class="ico"></span><span class="ico"></span><span class="on"><i></i>More</span></nav>
  </section>

  <!-- Row 2 labels -->
  <div class="label" style="left:134px;top:808px;width:200px">PILOTS<span>RADS_LIST_PAGE1</span></div>
  <div class="label" style="left:449px;top:808px;width:200px">CONTACTS<span>RADS_LISTPAGE2</span></div>
  <div class="label" style="left:751px;top:808px;width:200px">CONTACTS<span>SEARCH RESULTS</span></div>

  <!-- Pilots list -->
  <section class="screen" style="left:129px;top:880px;height:565px">
    <header class="hero"><div class="hero-photo" role="img" aria-label="Photo of pilots in uniform"></div>
      <div class="status"><span>12:30PM</span><span>▂▄ ◠<i></i></span></div>
      <div class="bar"><span class="back">‹</span><span class="title">Pilots</span><span class="pill">Add</span><span class="dots">···</span></div>
    </header>
    <div class="body" style="padding-top:18px;margin-top:0">
      <div class="search"><span>⌕</span><span class="grow">Search</span><span class="filter"></span></div>
      <div class="letter">A<span>⌄</span></div>
      <div class="item"><div class="avatar" role="img" aria-label="Pilot portrait photo"></div><div class="grow"><div class="name">Avery, Marcus Dean</div><div class="tags"><span class="tag t-id">3182133</span></div></div><span class="date">9/30/24</span></div>
      <div class="item"><div class="avatar" role="img" aria-label="Pilot portrait photo"></div><div class="grow"><div class="name">Ansel, Roland Quinn</div><div class="tags"><span class="tag t-id">4467155</span></div></div><span class="date">5/19/24</span></div>
      <div class="item"><div class="avatar" role="img" aria-label="Pilot portrait photo"></div><div class="grow"><div class="name">Arden, Mira, Sloane</div><div class="tags"><span class="tag t-id">4360575</span></div></div><span class="date">2/25/25</span></div>
      <div class="letter">B<span>⌄</span></div>
      <div class="item"><div class="avatar" role="img" aria-label="Pilot portrait photo"></div><div class="grow"><div class="name">Brandt, Owen, Felix</div><div class="tags"><span class="tag t-id">4360575</span></div></div><span class="date">9/30/24</span></div>
      <div class="item"><div class="avatar" role="img" aria-label="Pilot portrait photo"></div><div class="grow"><div class="name">Barlow, Henry</div><div class="tags"><span class="tag t-id">3423819</span></div></div><span class="date">2/28/25</span></div>
      <div class="letter">C<span>⌄</span></div>
      <div class="item"><div class="avatar" role="img" aria-label="Pilot portrait photo"></div><div class="grow"><div class="name">Corwin, Eli, Jaspar</div><div class="tags"><span class="tag t-id">2654896</span></div></div><span class="date">9/30/24</span></div>
    </div>
    <nav class="nav"><span class="ico"></span><span class="on"><i></i>Pilot</span><span class="ico"></span><span class="ico"></span><span class="ico"></span></nav>
  </section>

  <!-- Contacts list -->
  <section class="screen" style="left:444px;top:880px;height:617px">
    <header class="hero"><div class="hero-photo" role="img" aria-label="Photo of pilots in uniform"></div>
      <div class="status"><span>12:30PM</span><span>▂▄ ◠<i></i></span></div>
      <div class="bar"><span class="back">‹</span><span class="title">Contacts</span><span class="pill">Add</span><span class="dots">···</span></div>
    </header>
    <div class="body" style="padding-top:18px;margin-top:0">
      <div class="search"><span class="sel">All <span>⌄</span></span><span class="grow">Search</span><span>⌕</span></div>
      <div class="letter">A<span>⌄</span></div>
      <div class="item"><div class="avatar" role="img" aria-label="Contact portrait photo"></div><div class="grow"><div class="name">Avery, Marcus Dean</div><div class="tags"><span class="tag t-own">Aircraft Owner</span><span class="tag t-ent">Enthusiast -e</span></div></div></div>
      <div class="item"><div class="avatar" role="img" aria-label="Contact portrait photo"></div><div class="grow"><div class="name">Ansel, Roland Quinn</div><div class="tags"><span class="tag t-own">Aircraft Owner</span><span class="tag t-qual">Qualified Pilot</span><span class="tag t-pilot">Pilot</span></div></div></div>
      <div class="item"><div class="avatar" role="img" aria-label="Contact portrait photo"></div><div class="grow"><div class="name">Arden, Mira, Sloane</div><div class="tags"><span class="tag t-own">Aircraft Owner</span><span class="tag t-qual">Qualified Pilot</span></div></div></div>
      <div class="letter">B<span>⌄</span></div>
      <div class="item"><div class="avatar" role="img" aria-label="Contact portrait photo"></div><div class="grow"><div class="name">Brandt, Owen, Felix</div><div class="tags"><span class="tag t-pilot">Pilot</span></div></div><span class="date">9/30/24</span></div>
      <div class="item"><div class="avatar" role="img" aria-label="Contact portrait photo"></div><div class="grow"><div class="name">Barlow, Henry</div><div class="tags"><span class="tag t-pilot">Pilot</span></div></div><span class="date">2/28/25</span></div>
      <div class="letter">C<span>⌄</span></div>
      <div class="item"><div class="avatar" role="img" aria-label="Contact portrait photo"></div><div class="grow"><div class="name">Corwin, Eli, Jaspar</div><div class="tags"><span class="tag t-own">Aircraft Owner</span><span class="tag t-qual">Qualified Pilot</span><span class="tag t-pilot">Pilot</span></div></div></div>
      <div class="item"><div class="avatar" role="img" aria-label="Contact portrait photo"></div><div class="grow"><div class="name">Calder, Nolan, Reid</div><div class="tags"><span class="tag t-own">Aircraft Owner</span><span class="tag t-qual">Qualified Pilot</span><span class="tag t-pilot">Pilot</span></div></div></div>
    </div>
    <nav class="nav"><span class="on"><i></i>Contact</span><span class="ico"></span><span class="ico"></span><span class="ico"></span><span class="ico"></span></nav>
  </section>

  <!-- Search results -->
  <section class="screen" style="left:746px;top:880px;height:550px">
    <header class="hero"><div class="hero-photo" role="img" aria-label="Photo of pilots in uniform"></div>
      <div class="status"><span>12:30PM</span><span>▂▄ ◠<i></i></span></div>
      <div class="bar"><span class="back">‹</span><span class="title">Contacts</span><span class="pill">Add</span><span class="dots">···</span></div>
    </header>
    <div class="body" style="padding-top:18px;margin-top:0">
      <div class="search"><span class="sel">Aircraft Owner <span>⌄</span></span><span class="grow">Search</span><span>⌕</span></div>
      <div class="item"><div class="avatar" role="img" aria-label="Contact portrait photo"></div><div class="grow"><div class="name">Avery, Marcus Dean</div><div class="tags"><span class="tag t-own">Aircraft Owner</span><span class="tag t-ent">Enthusiast -e</span></div></div></div>
      <div class="item"><div class="avatar" role="img" aria-label="Contact portrait photo"></div><div class="grow"><div class="name">Ansel, Roland Quinn</div><div class="tags"><span class="tag t-own">Aircraft Owner</span><span class="tag t-qual">Qualified Pilot</span><span class="tag t-pilot">Pilot</span></div></div></div>
      <div class="item"><div class="avatar" role="img" aria-label="Contact portrait photo"></div><div class="grow"><div class="name">Arden, Mira, Sloane</div><div class="tags"><span class="tag t-own">Aircraft Owner</span><span class="tag t-qual">Qualified Pilot</span></div></div></div>
      <div class="item"><div class="avatar" role="img" aria-label="Contact portrait photo"></div><div class="grow"><div class="name">Corwin, Eli, Jaspar</div><div class="tags"><span class="tag t-own">Aircraft Owner</span><span class="tag t-qual">Qualified Pilot</span><span class="tag t-pilot">Pilot</span></div></div></div>
      <div class="item"><div class="avatar" role="img" aria-label="Contact portrait photo"></div><div class="grow"><div class="name">Calder, Nolan, Reid</div><div class="tags"><span class="tag t-own">Aircraft Owner</span><span class="tag t-qual">Qualified Pilot</span><span class="tag t-pilot">Pilot</span></div></div></div>
    </div>
  </section>

  <!-- Row 3 labels -->
  <div class="label" style="left:140px;top:1582px;width:200px">CONTACTS<span>RADS_READ_PAGE</span></div>
  <div class="label" style="left:455px;top:1582px;width:220px">CONTACTS<span>RADS_READ_PAGE2</span></div>
  <div class="label" style="left:770px;top:1582px;width:220px">PILOT DETAILS<span>RADS_READ_PAGE2</span></div>

  <!-- Read page -->
  <section class="screen" style="left:129px;top:1655px;height:545px">
    <header class="hero"><div class="hero-photo" role="img" aria-label="Aerial photo of an airliner above a runway"></div>
      <div class="status"><span>12:30PM</span><span>▂▄ ◠<i></i></span></div>
      <div class="bar"><span class="back">‹</span><span class="title">Contact</span><span class="dots">···</span></div>
    </header>
    <div class="body" style="padding-top:12px;margin-top:0">
      <div class="action"><span class="ring"><svg class="i"><use href="#user"/></svg></span>Add Personal Information -e</div>
      <div class="action"><span class="ring"><svg class="i"><use href="#case"/></svg></span>Add Work Info -e</div>
      <div class="action"><span class="ring"><svg class="i"><use href="#star"/></svg></span>Add Skills/Talents -e</div>
      <div class="action"><span class="ring"><svg class="i"><use href="#case"/></svg></span>Add Resources &nbsp;-e</div>
      <div class="block y">Pilots -e<div class="drop"><span>Ashby, Lionel, 3647946, 10/31/23</span><span>⌄</span></div></div>
      <div class="block b">Aircraft Owner -e<div class="drop"><span>Ashby, Lionel: Aerlo: 182T: Aerlo<br>Aircraft Company, Single Engine, 1100</span><span>⌄</span></div><span class="btn">Add Aircraft Owner</span></div>
      <div class="block g">Qualified Pilot -e<div class="drop"><span>Ashby, Lionel: Aerlo: 182T: Aerlo<br>Aircraft Company, Single Engine, 1100</span><span>⌄</span></div><span class="btn">Add Qualified Pilot -e</span></div>
    </div>
    <nav class="nav blue"><span class="on"><i></i>Contact</span><span class="ico"></span><span class="ico"></span><span class="ico"></span><span class="ico"></span></nav>
  </section>

  <!-- Read page 2 -->
  <section class="screen" style="left:444px;top:1655px;height:635px">
    <header class="hero"><div class="hero-photo" role="img" aria-label="Aerial photo of an airliner above a runway"></div>
      <div class="status"><span>12:30PM</span><span>▂▄ ◠<i></i></span></div>
      <div class="bar"><span class="back">‹</span><span class="title">Contact</span><span class="dots">···</span></div>
    </header>
    <div class="body" style="padding-top:12px;margin-top:0">
      <div class="action"><span class="ring"><svg class="i"><use href="#mail"/></svg></span>Add Email -e</div>
      <div class="action"><span class="ring"><svg class="i"><use href="#arrow"/></svg></span>Add Social Media -e</div>
      <div class="action"><span class="ring"><svg class="i"><use href="#phone"/></svg></span>Add Emergency Contact -e</div>
      <div class="action"><span class="ring"><svg class="i"><use href="#user"/></svg></span>Add Personal Information -e</div>
      <div class="action"><span class="ring"><svg class="i"><use href="#case"/></svg></span>Add Work Info -e</div>
      <div class="action"><span class="ring"><svg class="i"><use href="#star"/></svg></span>Add Skills/Talents -e</div>
      <div class="action"><span class="ring"><svg class="i"><use href="#case"/></svg></span>Add Resources &nbsp;-e</div>
      <div class="block y">Pilots -e<div class="drop"><span>Ashby, Lionel, 3647946, 10/31/23</span><span>⌄</span></div></div>
      <div class="block b">Aircraft Owner -e<div class="drop"><span>Ashby, Lionel: Aerlo: 182T: Aerlo<br>Aircraft Company, Single Engine, 1100</span><span>⌄</span></div><span class="btn full">Add Aircraft Owner</span></div>
      <div class="block g">Qualified Pilot -e<div class="drop"><span>Ashby, Lionel: Aerlo: 182T: Aerlo<br>Aircraft Company, Single Engine, 1100</span><span>⌄</span></div><span class="btn full">Add Qualified Pilot -e</span></div>
    </div>
    <nav class="nav blue"><span class="on"><i></i>Contact</span><span class="ico"></span><span class="ico"></span><span class="ico"></span><span class="ico"></span></nav>
  </section>

  <!-- Pilot details -->
  <section class="screen" style="left:760px;top:1655px;height:580px">
    <header class="hero"><div class="hero-photo" role="img" aria-label="Photo of pilots in uniform"></div>
      <div class="status"><span>12:30PM</span><span>▂▄ ◠<i></i></span></div>
      <div class="bar"><span class="back">‹</span><span class="title">Pilot</span><span class="dots">···</span></div>
    </header>
    <div class="body" style="padding-top:12px;margin-top:0">
      <div class="box">
        <div class="field"><span class="ring"><svg class="i"><use href="#user"/></svg></span><div><small>Pilot -e</small><b>Avery, Marcus, Dean</b></div></div>
        <div class="field"><span class="ring"><svg class="i"><use href="#case"/></svg></span><div><small>Pilot Certificate No -e</small><b>3182133</b></div></div>
        <div class="field"><span class="ring"><svg class="i"><use href="#shield"/></svg></span><div><small>Medical Expiration Date -e</small><b>9/30/24</b></div></div>
        <div class="field"><span class="ring"><svg class="i"><use href="#cal"/></svg></span><div><small>Flight Review Expiration Date -e</small><b>6/30/24</b></div></div>
        <div class="field"><span class="ring"><svg class="i"><use href="#plane"/></svg></span><div><small>Total Flight Time -e</small><b>2500</b></div></div>
      </div>
      <div class="box" style="padding:6px">
        <div class="drop" style="display:flex;justify-content:space-between;border:1px solid var(--line);border-radius:4px;padding:6px 8px;font-size:6.5px;line-height:1.5;margin-bottom:6px"><span>Ashby, Lionel: Aerlo: 182T: Aerlo<br>Aircraft Company, Single Engine, 1100</span><span>⌄</span></div>
        <div class="drop" style="display:flex;justify-content:space-between;border:1px solid var(--line);border-radius:4px;padding:6px 8px;font-size:6.5px;line-height:1.5;margin-bottom:6px"><span>Ashby, Lionel: Aerlo: 182T: Aerlo<br>Aircraft Company, Single Engine, 1100</span><span>⌄</span></div>
        <span class="btn full">Add Base Airport -e</span>
      </div>
      <div class="action"><span class="ring"><svg class="i"><use href="#star"/></svg></span>Add Ratings -s</div>
      <div class="box">
        <div class="field"><span class="ring"><svg class="i"><use href="#user"/></svg></span><div><small>Contact -e</small><b>Tessa Morrow</b></div></div>
        <div class="field"><span class="ring"><svg class="i"><use href="#phone"/></svg></span><div><small>Phone -e</small><b>555-014-2290</b></div></div>
        <div class="field"><div><small>Medical Expiration Date -e</small></div></div>
      </div>
    </div>
    <nav class="nav blue">
      <span class="tab"><span class="ico"></span>Contact</span>
      <span class="tab cur"><span class="ico"></span>Pilot</span>
      <span class="tab"><span class="ico"></span>Plane</span>
      <span class="tab"><span class="ico"></span>FX Request</span>
      <span class="tab"><span class="ico"></span>More</span>
    </nav>
  </section>
  <div class="pointer"></div>
  <div class="label" style="left:765px;top:2268px;width:200px;font-size:18px">ADDED MENU NAME BELOW</div>

</main>
</body>
</html>
```